"Harbor Builders" is a residential building company and needs a new business card design and may re

We would like a redesign based on the existing logo, and would like to see a new font as well. We are bespoke home builders who build sustainable energy efficient homes.

Industry/Entity Type

Construction

Contact Information for Business Card

Business card size 40mm x 90mm

Colors

Designer to choose colors to be used in the design.

```html
<!DOCTYPE html>
<html lang="en">
<head>
<meta charset="utf-8">
<title>Harbor Builders – Business Card</title>
<link rel="stylesheet" href="https://fonts.googleapis.com/css2?family=Roboto:wght@400;500;700&family=Roboto+Condensed:wght@700&display=swap">
<style>
  :root {
    --backdrop: #2e2e2e;
    --card-dark: #1f1f1f;
    --card-light: #f3f3f3;
    --accent: #a6c83a;
    --ink: #111111;
    --ink-soft: #4a4a4a;
    --white: #ffffff;
    --muted: #d8d8d8;
  }
  * { box-sizing: border-box; margin: 0; padding: 0; }
  html, body { width: 1200px; height: 900px; overflow: hidden; }
  body {
    background: var(--backdrop);
    font-family: "Roboto", Arial, sans-serif;
    position: relative;
  }
  .card {
    position: absolute;
    left: 220px;
    width: 760px;
    height: 338px;
  }
  .card-front { top: 70px; background: var(--card-dark); }
  .card-back { top: 480px; background: var(--card-light); }

  .brand {
    position: absolute;
    top: 110px;
    left: 0;
    width: 100%;
    display: flex;
    justify-content: center;
    align-items: center;
    gap: 18px;
  }
  .brand-square {
    width: 46px;
    height: 46px;
    background: var(--accent);
  }
  .brand-name {
    font-family: "Roboto", Arial, sans-serif;
    font-weight: 500;
    font-size: 54px;
    letter-spacing: 1px;
    color: var(--white);
    line-height: 1;
  }
  .front-web {
    position: absolute;
    bottom: 52px;
    width: 100%;
    text-align: center;
    font-size: 17px;
    letter-spacing: 4px;
    color: var(--white);
  }
  .front-web .domain { color: var(--accent); }

  .holder-name {
    position: absolute;
    top: 110px;
    left: 70px;
    font-family: "Roboto Condensed", "Arial Narrow", sans-serif;
    font-weight: 700;
    font-size: 36px;
    color: var(--ink);
    letter-spacing: 0.5px;
  }
  .divider {
    position: absolute;
    top: 92px;
    left: 350px;
    width: 1px;
    height: 100px;
    background: linear-gradient(to bottom, transparent, #9a9a9a, transparent);
  }
  .contact-list {
    position: absolute;
    top: 100px;
    left: 375px;
    list-style: none;
    font-size: 18px;
    color: var(--ink-soft);
  }
  .contact-list li {
    display: flex;
    align-items: center;
    gap: 12px;
    height: 27px;
  }
  .contact-list svg { width: 16px; height: 16px; flex: none; }
  .company-details {
    position: absolute;
    bottom: 38px;
    width: 100%;
    text-align: center;
    font-size: 18px;
    line-height: 1.35;
    color: var(--ink-soft);
  }
  .company-details .company-name { font-weight: 700; }
</style>
</head>
<body>
  <section class="card card-front">
    <div class="brand">
      <span class="brand-square"></span>
      <span class="brand-name">harbor builders</span>
    </div>
    <p class="front-web">www.<span class="domain">harborbuilders</span>.com.au</p>
  </section>

  <section class="card card-back">
    <h1 class="holder-name">DANIEL MORETTI</h1>
    <span class="divider"></span>
    <ul class="contact-list">
      <li>
        <svg viewBox="0 0 16 16" aria-hidden="true"><rect x="4" y="1" width="8" height="14" rx="1.5" fill="none" stroke="#111" stroke-width="1.6"/><line x1="7" y1="12.5" x2="9" y2="12.5" stroke="#111" stroke-width="1.4"/></svg>
        0400 555 018
      </li>
      <li>
        <svg viewBox="0 0 16 16" aria-hidden="true"><rect x="1" y="3.5" width="14" height="9" fill="#111"/><polyline points="1,3.5 8,9 15,3.5" fill="none" stroke="#f3f3f3" stroke-width="1.2"/></svg>
        daniel@harborbuilders.com.au
      </li>
      <li>
        <svg viewBox="0 0 16 16" aria-hidden="true"><circle cx="8" cy="8" r="7" fill="#111"/><ellipse cx="8" cy="8" rx="3" ry="7" fill="none" stroke="#f3f3f3" stroke-width="1"/><line x1="1" y1="8" x2="15" y2="8" stroke="#f3f3f3" stroke-width="1"/></svg>
        www.harborbuilders.com.au
      </li>
    </ul>
    <address class="company-details" style="font-style:normal">
      <span class="company-name">Harbor Builders Pty Ltd</span><br>
      PO Box 4120 Eastgate, LPO Kelmore WA 6099<br>
      Registration 10483 | ABN: 52 604 391 887
    </address>
  </section>
</body>
</html>
```